Vale Crest - Business Cards

We are a consultancy to help builders to optimize their planning in order to save building costs. For that reason we need a clean and professional business card for our high-priced services. A QR code should lead to the contact information needed.

```html
<!DOCTYPE html>
<html lang="de">
<head>
<meta charset="utf-8">
<title>Vale Crest – Business Cards</title>
<link href="https://fonts.googleapis.com/css2?family=Roboto:wght@400;500;700&family=Michroma&display=swap" rel="stylesheet">
<style>
  :root {
    --backdrop: #2a2a2b;
    --card-top: #1c1c1d;
    --card-bottom: #28282a;
    --gold: #c9a24a;
    --gold-light: #e0bd63;
    --gold-dark: #a67c2c;
    --silver: #b9b9bc;
    --text-light: #e6e6e6;
    --ink-dark: #1b1b1b;
    --emboss: #101011;
  }
  * { margin: 0; padding: 0; box-sizing: border-box; }
  html, body { width: 1200px; height: 1138px; overflow: hidden; }
  body {
    background: var(--backdrop);
    font-family: "Roboto", Arial, sans-serif;
    position: relative;
  }
  .card {
    position: absolute;
    border-radius: 16px;
    background: linear-gradient(160deg, var(--card-top), var(--card-bottom));
    overflow: hidden;
  }
  .card--front { left: 274px; top: 186px; width: 624px; height: 376px; }
  .card--back  { left: 276px; top: 608px; width: 618px; height: 374px; }

  /* front */
  .front-lockup {
    position: absolute;
    left: 0; right: 0; top: 86px;
    display: flex; flex-direction: column; align-items: center;
  }
  .front-lockup__mark {
    width: 96px; height: 96px;
    border: 4px solid var(--emboss);
  }
  .front-lockup__name {
    margin-top: 30px;
    font-weight: 700;
    font-size: 44px;
    line-height: 40px;
    letter-spacing: 6px;
    color: var(--emboss);
  }
  .front-lockup__tagline {
    margin-top: 10px;
    font-family: "Michroma", sans-serif;
    font-size: 15px;
    line-height: 18px;
    letter-spacing: 4px;
    color: var(--emboss);
  }

  /* back */
  .back-lockup {
    position: absolute;
    left: 36px; top: 60px;
    display: flex; align-items: center; gap: 22px;
  }
  .back-lockup__mark {
    width: 72px; height: 72px;
    border: 3px solid var(--gold);
  }
  .back-lockup__name {
    font-weight: 700;
    font-size: 36px;
    line-height: 34px;
    letter-spacing: 4px;
    color: var(--gold);
  }
  .back-lockup__tagline {
    margin-top: 6px;
    font-family: "Michroma", sans-serif;
    font-size: 13px;
    line-height: 16px;
    letter-spacing: 3px;
    color: var(--gold);
  }
  .person { position: absolute; left: 36px; top: 208px; }
  .person__name { font-weight: 500; font-size: 24px; line-height: 28px; color: var(--gold); }
  .person__role { font-size: 16px; line-height: 22px; color: var(--text-light); margin-top: 2px; }
  .address {
    position: absolute; left: 36px; top: 294px;
    font-style: normal;
    font-size: 16px; line-height: 24px; color: var(--text-light);
  }
  .contacts {
    position: absolute; left: 326px; top: 230px;
    list-style: none;
  }
  .contacts li {
    display: flex; align-items: center; gap: 16px;
    font-size: 17px; line-height: 24px; color: var(--text-light);
  }
  .contacts svg { width: 16px; height: 16px; flex: none; }
  .gold-band {
    position: absolute; right: 0; bottom: 0;
    width: 354px; height: 46px;
    background: linear-gradient(90deg, var(--gold-dark), var(--gold-light) 55%, var(--gold-dark));
    clip-path: polygon(28px 0, 100% 0, 100% 100%, 0 100%);
  }
  .gold-band__text {
    position: absolute; left: 70px; top: 15px;
    font-family: "Michroma", sans-serif;
    font-size: 12px; line-height: 16px; letter-spacing: 1.5px;
    color: var(--ink-dark);
    white-space: nowrap;
  }
  .silver-strip {
    position: absolute; left: 0; bottom: 0;
    width: 280px; height: 14px;
    background: linear-gradient(90deg, #2a2a2c, #5a5a5e 40%, var(--silver) 60%, #55555a 75%, #2a2a2c);
  }
</style>
</head>
<body>
  <section class="card card--front" aria-label="Card front">
    <div class="front-lockup">
      <div class="front-lockup__mark"></div>
      <div class="front-lockup__name">VALE CREST</div>
      <div class="front-lockup__tagline">WEIL JEDER EURO ZÄHLT</div>
    </div>
  </section>

  <section class="card card--back" aria-label="Card back">
    <div class="back-lockup">
      <div class="back-lockup__mark"></div>
      <div>
        <div class="back-lockup__name">VALE CREST</div>
        <div class="back-lockup__tagline">WEIL JEDER EURO ZÄHLT</div>
      </div>
    </div>

    <div class="person">
      <div class="person__name">Vale Crest</div>
      <div class="person__role">Managing Director</div>
    </div>
    <address class="address">48 Lindenweg, Nordstadt,<br>Bremen, DE 28195</address>

    <ul class="contacts">
      <li><svg viewBox="0 0 16 16"><path fill="#c9a24a" d="M3 2h3l1 3-2 1a8 8 0 0 0 5 5l1-2 3 1v3a1 1 0 0 1-1 1A12 12 0 0 1 2 3a1 1 0 0 1 1-1z"/></svg>0421-555-0186</li>
      <li><svg viewBox="0 0 16 16"><path d="M1 3h14v10H1z M2 4l6 5 6-5" fill="none" stroke="#c9a24a" stroke-width="1.5"/></svg>kontakt@valecrest.de</li>
      <li><svg viewBox="0 0 16 16"><circle cx="8" cy="8" r="6.5" fill="none" stroke="#c9a24a" stroke-width="1.3"/><path d="M1.5 8h13M8 1.5c-3 3-3 10 0 13M8 1.5c3 3 3 10 0 13" fill="none" stroke="#c9a24a" stroke-width="1.1"/></svg>www.valecrest.de</li>
    </ul>

    <div class="silver-strip"></div>
    <div class="gold-band"><span class="gold-band__text">WEIL JEDER EURO ZÄHLT</span></div>
  </section>
</body>
</html>
```